Alaska Law Firm Needs a Sticker Design

We need a design for stickers to put on already-printed brochures. We mail the brochures to potential clients so they can learn more about accident-induced injuries, insurance claims, legal representation, and our own law firm.

One of our lawyers wrote a book that provides a helpful overview of personal injury claims. We are offering this book for free to anyone who calls and requests it. Therefore, the sticker design should include one of the following phrases, or something very similar:
a) "Still have questions? Call and request our book-- for free!"
b) "Still have questions about auto accident claims? Call and request our book today."
c) "Still have questions about filing a claim? Call and request a free copy of our book."
d) "Still have questions? Call us today to request a free copy of our book, Clear Lanes Ahead."
e) "To learn more about automobile accidents and insurance, call today and request a free copy of our book."

The sticker should be approximately 3"x3" and may be a circle, square, rectangle, or ellipsis. The sticker will be placed on the back of the folder, which is light blue. We would like the sticker to match the color scheme of our website and the folder.

I will upload an image of the book cover as soon as I obtain it.

Law Firm

Font styles to use
Serif
Sans Serif

Requirements
Should not have
• Bright colors that aren't already used in the folder design. e.g. no bright orange, pink, chartreuse, turquoise, yellow, red.

```html
<!DOCTYPE html>
<html lang="en">
<head>
<meta charset="utf-8">
<title>Still Have Questions Sticker</title>
<link rel="stylesheet" href="https://fonts.googleapis.com/css2?family=Ubuntu:wght@500;700&family=Kurale&display=swap">
<style>
  :root {
    --navy: #1f2d85;
    --navy-deep: #17226a;
    --ink: #262626;
    --paper: #f7f7f7;
    --paper-shade: #e6e6e6;
    --bg-light: #f8f8f8;
    --bg-mid: #c9c9c9;
  }
  html, body {
    margin: 0;
    padding: 0;
    overflow: hidden;
  }
  .canvas {
    width: 1200px;
    height: 1200px;
    background: radial-gradient(ellipse at 50% 20%, var(--bg-light) 0%, #e4e4e4 45%, var(--bg-mid) 100%);
    position: relative;
    overflow: hidden;
  }
  .sticker {
    display: block;
    width: 1200px;
    height: 1200px;
  }
  .headline {
    font-family: "Ubuntu", sans-serif;
    font-weight: 700;
  }
  .headline-dark { fill: var(--ink); }
  .headline-accent { fill: var(--navy); }
  .headline-band { fill: #ffffff; }
  .offer {
    font-family: "Kurale", serif;
  }
  .offer-line { fill: var(--ink); font-size: 46px; }
  .offer-free { fill: var(--navy); font-size: 104px; }
</style>
</head>
<body>
<div class="canvas">
  <svg class="sticker" viewBox="0 0 1300 1300" xmlns="http://www.w3.org/2000/svg" role="img" aria-label="Sticker: Still have questions? Call and request our book for free!">
    <defs>
      <linearGradient id="frameFill" x1="0" y1="0" x2="0" y2="1">
        <stop offset="0" stop-color="#243294"/>
        <stop offset="1" stop-color="#1a2678"/>
      </linearGradient>
      <linearGradient id="bandFill" x1="0" y1="0" x2="1" y2="0">
        <stop offset="0" stop-color="#1a2570"/>
        <stop offset="0.5" stop-color="#223190"/>
        <stop offset="1" stop-color="#1a2570"/>
      </linearGradient>
      <linearGradient id="paperFill" x1="0" y1="0" x2="0" y2="1">
        <stop offset="0" stop-color="#e8e8e8"/>
        <stop offset="0.5" stop-color="#fbfbfb"/>
        <stop offset="1" stop-color="#e4e4e4"/>
      </linearGradient>
      <filter id="softShadow" x="-10%" y="-10%" width="120%" height="120%">
        <feDropShadow dx="0" dy="4" stdDeviation="6" flood-color="#000" flood-opacity="0.25"/>
      </filter>
      <filter id="textShadow">
        <feDropShadow dx="0" dy="3" stdDeviation="3" flood-color="#000" flood-opacity="0.35"/>
      </filter>
    </defs>

    <g class="sticker-shape" filter="url(#softShadow)">
      <path class="sticker-frame" fill="url(#frameFill)"
        d="M335,148 L965,148 C1075,195 1118,280 1118,360 C1118,430 1090,480 1058,518 L1155,590 L1155,690 L1110,690 C1090,820 990,930 820,968 C720,990 670,1040 650,1135 C630,1040 580,990 480,968 C310,930 210,820 190,690 L143,690 L143,590 L240,518 C210,480 180,430 180,360 C180,280 225,195 335,148 Z"/>
      <path class="sticker-band" fill="url(#bandFill)"
        d="M240,518 L1058,518 L1155,590 L1155,690 L143,690 L143,590 Z"/>
      <path class="sticker-top" fill="url(#paperFill)"
        d="M355,182 L945,182 C1040,225 1085,290 1085,360 C1085,430 1060,480 1035,518 L265,518 C240,480 213,430 213,360 C213,290 258,225 355,182 Z"/>
      <path class="sticker-bottom" fill="url(#paperFill)"
        d="M192,693 L1108,693 C1085,810 990,900 820,935 C710,960 665,1010 650,1095 C635,1010 590,960 480,935 C310,900 215,810 192,693 Z"/>
    </g>

    <text class="headline" x="650" y="428" text-anchor="middle" font-size="142">
      <tspan class="headline-dark">Still</tspan>
      <tspan class="headline-accent">have</tspan>
    </text>
    <text class="headline headline-band" x="648" y="648" text-anchor="middle" font-size="136" filter="url(#textShadow)">Questions?</text>

    <text class="offer offer-line" x="648" y="755" text-anchor="middle">Call and request our book</text>
    <text class="offer offer-free" x="650" y="880" text-anchor="middle">for free!</text>
  </svg>
</div>
</body>
</html>
```